ProfileNet background/title banner

Feel free to visit my website (kvtcheckup.ca) and current ProfilNet (KVT Property Inspections) page for a general feel. We focus on our trades background and experience. I have uploaded some logos that I would like used here. We offer Commercial, Residential, Agricultural inspections. With 24/7 online booking and call center.
Updates
Please ensure the small logos are added. Try to use all 3 colors. Red, Grey, Black (and some white), leave room for the profile pic that appear in the bottom left as well.
Target Market(s)
realtors and real estate professionals
Industry/Entity Type
Property Inspections for Real Estate
Logo Text
"Inspected by Tradesmen"
Requirements
Must have
- To be simple with the key highlights and logos.

```html
<!DOCTYPE html>
<html lang="en">
<head>
<meta charset="utf-8">
<title>Residential &amp; Commercial Inspections Banner</title>
<link href="https://fonts.googleapis.com/css2?family=Montserrat:wght@300;400;500;600&display=swap" rel="stylesheet">
<style>
  :root {
    --maroon-deep: #3e0709;
    --maroon: #5c0f13;
    --maroon-soft: #7a1a1e;
    --red: #e3202a;
    --red-dark: #b3141c;
    --white: #ffffff;
    --grey: #d9d4d2;
    --photo-sky: #a9c4d6;
    --photo-warm: #c98f72;
    --photo-roof: #6e3b2c;
  }
  * { margin: 0; padding: 0; box-sizing: border-box; }
  html, body {
    width: 1200px; height: 203px; overflow: hidden;
    background: var(--maroon-deep);
  }
  .banner {
    position: relative; width: 1200px; height: 203px; overflow: hidden;
    font-family: "Montserrat", sans-serif; color: var(--white);
  }
  .banner__art { position: absolute; inset: 0; }
  .headline { position: absolute; left: 40px; top: 16px; line-height: 1; width: 153px; }
  .headline__kicker {
    display: block; font-size: 8.9px; font-weight: 500; letter-spacing: 0.25px; white-space: nowrap;
  }
  .headline__main {
    display: block; font-size: 20.5px; font-weight: 400; letter-spacing: 0.9px; margin-top: 2px; white-space: nowrap;
  }
  .services {
    position: absolute; right: 204px; top: 54px; list-style: none; text-align: right;
  }
  .services li {
    font-size: 9.6px; font-weight: 300; letter-spacing: 0.55px; line-height: 15.8px; white-space: nowrap;
  }
  .partners {
    position: absolute; left: 1016px; top: 58px; width: 156px;
    display: grid; grid-template-columns: 78px 78px; grid-auto-rows: 28px; row-gap: 27px; align-items: center;
  }
  .partner {
    display: flex; align-items: center; justify-content: center; gap: 4px;
    font-size: 8.5px; font-weight: 600; letter-spacing: 0.3px; color: var(--white);
    text-align: center; line-height: 1.1; height: 28px; white-space: nowrap;
  }
  .partner__mark { width: 7px; height: 7px; background: var(--white); flex: none; }
  .partner__mark--round { border-radius: 50%; }
</style>
</head>
<body>
<main class="banner">
  <svg class="banner__art" viewBox="0 0 1200 203" width="1200" height="203">
    <defs>
      <linearGradient id="bgTone" x1="0" y1="0" x2="1" y2="1">
        <stop offset="0" stop-color="#4a0a0d"/>
        <stop offset="0.5" stop-color="#5c0f13"/>
        <stop offset="1" stop-color="#430809"/>
      </linearGradient>
      <linearGradient id="photoTone" x1="0" y1="0" x2="0" y2="1">
        <stop offset="0" stop-color="var(--photo-sky)"/>
        <stop offset="0.3" stop-color="var(--photo-roof)"/>
        <stop offset="0.6" stop-color="var(--photo-warm)"/>
        <stop offset="1" stop-color="#e6d2c6"/>
      </linearGradient>
    </defs>

    <rect class="backdrop" width="1200" height="203" fill="url(#bgTone)" role="img" aria-label="Faint red-toned row of houses behind the banner"/>

    <g class="guide-lines" stroke="#8a1f24" stroke-width="0.8" fill="none" opacity="0.8">
      <line x1="120" y1="0" x2="0" y2="140"/>
      <line x1="245" y1="40" x2="135" y2="163"/>
      <line x1="920" y1="0" x2="760" y2="190"/>
      <line x1="1110" y1="0" x2="950" y2="190"/>
      <line x1="1200" y1="40" x2="1080" y2="180"/>
      <line x1="900" y1="45" x2="860" y2="45"/>
      <line x1="900" y1="47" x2="960" y2="0"/>
    </g>

    <polygon class="photo" points="305,0 838,0 666,203 140,203" fill="url(#photoTone)"
      role="img" aria-label="Row of colourful Victorian townhouses in front of a city skyline"/>

    <g class="stripes">
      <polygon points="288,0 306,0 176,156 158,156" fill="var(--red)"/>
      <polygon points="240,40 252,40 150,163 138,163" fill="var(--red-dark)" opacity="0.8"/>
      <polygon points="150,163 290,163 290,165 148,165" fill="var(--red)" opacity="0.6"/>
      <polygon points="838,0 858,0 686,203 666,203" fill="var(--red)"/>
      <polygon points="870,0 890,0 735,185 715,185" fill="var(--red-dark)" opacity="0.75"/>
    </g>

    <circle class="standard-seal" cx="773" cy="87" r="44" fill="var(--red)" stroke="var(--white)" stroke-width="1.5"/>
  </svg>

  <header class="headline">
    <span class="headline__kicker">RESIDENTIAL &amp; COMMERCIAL</span>
    <span class="headline__main">INSPECTIONS</span>
  </header>

  <ul class="services">
    <li>PROPERTY INSPECTION</li>
    <li>MOLD &amp; ASBESTOS TESTING</li>
    <li>ACREAGE INSPECTIONS</li>
    <li>PRE-PURCHASE INSPECTIONS</li>
    <li>OZONE/ODOR TREATMENT</li>
    <li>HSTC INSPECTIONS</li>
  </ul>

  <div class="partners">
    <div class="partner"><span class="partner__mark"></span>THERMIQ</div>
    <div class="partner">Hearth Safety<br>Training</div>
    <div class="partner"><span class="partner__mark partner__mark--round"></span>Point Trail</div>
    <div class="partner"><span class="partner__mark"></span>Home Ledger</div>
  </div>
</main>
</body>
</html>
```